Technical Communications firm needs an article turned into a white paper

We want to redesign a 3-part blog series into a white paper that we can print for a conference. I've consolidated the three posts into the attached Word document.

We are looking for a light, easy to read design. Good use of graphics to support the message. I've added the graphics we used in the original post.

You can view them at
http://www.brightquillpages.com/blog/are-you-satisfied-with-your-dita-solution/

Target Market(s)

Product managers from High-tech, Finance, and Medical industries.

Industry/Entity Type

Information Technology

Colors

Designer to choose colors to be used in the design.

Requirements
Must have
• Must be modern, light, easy to read and slick design. Try to incorporate the graphics provided, but feel free to add more. Must retain the lists and tables.
• Must align with our website/brand.
• Must be easy to read. So not too busy.
• Please move all footnotes to endnotes. You'll need to rework the numbering.
Nice to have
• Awesome coverpage.
Should not have
• Hokey clipart. Not too heavy or hard to read.

```html
<!DOCTYPE html>
<html lang="en">
<head>
<meta charset="utf-8">
<title>Are you satisfied with your DITA solution? – White paper cover</title>
<link rel="stylesheet" href="https://fonts.googleapis.com/css2?family=Open+Sans:wght@300;400;600;700&display=swap">
<style>
  :root {
    --backdrop: #e9e6e1;
    --paper: #f2f3f5;
    --paper-shade: #e4e6ea;
    --navy: #0c3f8c;
    --navy-deep: #0a357a;
    --cyan: #27b2df;
    --sky-top: #3f78c4;
    --sky-mid: #9dc0e8;
    --sky-light: #eef4fb;
    --ink-blue: #1a4f9c;
    --ink-grey: #4a4f57;
    --white: #ffffff;
  }
  * { box-sizing: border-box; margin: 0; padding: 0; }
  html, body {
    width: 1200px; height: 804px; overflow: hidden;
    background: var(--backdrop);
    font-family: "Open Sans", Arial, sans-serif;
  }
  .cover {
    position: absolute; left: 338px; top: 32px;
    width: 524px; height: 740px;
    background: linear-gradient(180deg, var(--paper) 0%, var(--paper-shade) 100%);
    box-shadow: 0 8px 24px rgba(0,0,0,.18);
    overflow: hidden;
  }
  .cover__hero {
    position: absolute; left: 0; top: 0; width: 100%; height: 320px;
    background:
      radial-gradient(ellipse at 70% 55%, var(--sky-light) 0%, rgba(238,244,251,0) 55%),
      linear-gradient(160deg, var(--sky-top) 0%, var(--sky-mid) 55%, var(--sky-light) 100%);
  }
  .cover__band {
    position: absolute; left: 0; top: 300px; width: 100%; height: 206px;
    background: linear-gradient(180deg, var(--navy-deep) 0%, var(--navy) 100%);
  }
  .cover__title {
    position: absolute; left: 40px; top: 372px; width: 300px;
    color: var(--white); font-weight: 400; font-size: 31px; line-height: 1.22;
    letter-spacing: .2px;
  }
  .cover__url {
    position: absolute; left: 40px; top: 486px;
    color: var(--white); font-size: 9px; letter-spacing: 2.2px;
  }
  .cover__stripe {
    position: absolute; left: 0; top: 506px; width: 100%; height: 9px;
    background: var(--cyan);
  }
  .cover__photo {
    position: absolute; width: 128px; height: 128px; border-radius: 50%;
    border: 4px solid var(--paper);
  }
  .cover__photo--anchor {
    left: 262px; top: 448px;
    background: radial-gradient(circle at 50% 40%, #f4f4f4 0%, #c9cbcf 100%);
  }
  .cover__photo--question {
    left: 386px; top: 440px;
    background: radial-gradient(circle at 50% 70%, #d9b49a 0%, #2f8f6c 45%, #1f6f52 100%);
  }
  .cover__byline {
    position: absolute; left: 300px; top: 598px;
  }
  .cover__author {
    color: var(--ink-blue); font-weight: 700; font-size: 12px;
  }
  .cover__role {
    margin-top: 4px; color: var(--ink-grey); font-size: 7.5px;
  }
  .cover__brand {
    position: absolute; left: 40px; top: 652px;
    display: flex; align-items: center; gap: 8px;
  }
  .cover__brand-dot {
    width: 34px; height: 34px; border-radius: 50%; background: var(--navy);
  }
  .cover__brand-name {
    color: var(--navy); font-weight: 700; font-size: 15px; line-height: 1.05;
    width: 90px;
  }
</style>
</head>
<body>
  <main class="cover">
    <div class="cover__hero" role="img" aria-label="Hands holding a tablet as printed pages and letters fly out of its screen against a blue sky"></div>
    <section class="cover__band">
    </section>
    <h1 class="cover__title">Are you satisfied with your DITA solution?</h1>
    <p class="cover__url">www.brightquillpages.com</p>
    <div class="cover__stripe"></div>
    <div class="cover__photo cover__photo--anchor" role="img" aria-label="An anchor lifted by a red balloon against a grey sky"></div>
    <div class="cover__photo cover__photo--question" role="img" aria-label="A puzzled man looking up at a green chalkboard reading What am I supposed to do"></div>
    <div class="cover__byline">
      <p class="cover__author">By Dana Mercer</p>
      <p class="cover__role">President of Bright Quill Authoring Solutions Inc.</p>
    </div>
    <div class="cover__brand">
      <span class="cover__brand-dot"></span>
      <span class="cover__brand-name">BRIGHT QUILL PAGES</span>
    </div>
  </main>
</body>
</html>
```